Frostvale Harborline LLC

we need a business card design

Industry/Entity Type

hvac

Contact Information for Business Card

my logo

Requirements
Must have
• my logo and same colors

```html
<!DOCTYPE html>
<html lang="en">
<head>
<meta charset="utf-8">
<title>Frostvale Harborline LLC — Business Card</title>
<link rel="stylesheet" href="https://fonts.googleapis.com/css2?family=Roboto:wght@400;700&display=swap">
<style>
  :root {
    --bg: #e4e5e8;
    --card: #ffffff;
    --sky: #1aa9e0;
    --navy: #1b5aa6;
    --amber: #f7a21b;
    --gold: #fcc73a;
    --ink: #2b2b2b;
    --muted: #555a60;
  }
  * { box-sizing: border-box; margin: 0; padding: 0; }
  html, body {
    width: 1200px; height: 800px; overflow: hidden;
    background: var(--bg);
    font-family: "Roboto", Arial, sans-serif;
  }
  .stage {
    width: 1200px; height: 800px;
    display: flex; align-items: center; justify-content: center; gap: 60px;
  }
  .card {
    width: 520px; height: 297px;
    background: var(--card);
    position: relative;
    box-shadow: 0 6px 18px rgba(0,0,0,0.12);
  }
  .card--front { border: 12px solid var(--sky); display: flex; align-items: center; justify-content: center; }
  .card--back {
    border: 12px solid;
    border-image: linear-gradient(135deg, var(--amber), var(--gold)) 1;
    padding: 26px 30px;
  }
  .brand { display: flex; align-items: center; gap: 10px; }
  .brand__dot { width: 18px; height: 18px; border-radius: 50%; background: var(--amber); flex: none; }
  .brand__name { font-weight: 700; color: var(--navy); font-size: 26px; letter-spacing: 0.5px; }
  .card--back .brand { position: absolute; right: 26px; bottom: 30px; }
  .card--back .brand__name { font-size: 19px; }
  .person__name { color: var(--sky); font-weight: 700; font-size: 17px; text-transform: uppercase; }
  .person__role { color: var(--muted); font-size: 13px; margin-top: 2px; }
  .address { color: var(--ink); font-size: 13px; line-height: 1.4; margin-top: 16px; }
  .contact { list-style: none; margin-top: 12px; }
  .contact li { display: flex; align-items: center; gap: 8px; font-size: 13px; color: var(--ink); line-height: 1.55; }
  .contact svg { width: 12px; height: 12px; fill: var(--navy); flex: none; }
</style>
</head>
<body>
<main class="stage">
  <section class="card card--front" aria-label="Card front">
    <div class="brand">
      <span class="brand__dot"></span>
      <span class="brand__name">Frostvale Harborline LLC</span>
    </div>
  </section>

  <section class="card card--back" aria-label="Card back">
    <p class="person__name">Jordan Ellis</p>
    <p class="person__role">Director</p>
    <p class="address">00 dummy city<br>dummy place 0000</p>
    <ul class="contact">
      <li><svg viewBox="0 0 24 24"><path d="M6.6 10.8a15 15 0 0 0 6.6 6.6l2.2-2.2c.3-.3.7-.4 1-.2 1.1.4 2.3.6 3.6.6.6 0 1 .4 1 1V20c0 .6-.4 1-1 1A17 17 0 0 1 3 4c0-.6.4-1 1-1h3.5c.6 0 1 .4 1 1 0 1.3.2 2.5.6 3.6.1.3 0 .7-.2 1z"/></svg>555-014-2290</li>
      <li><svg viewBox="0 0 24 24"><path d="M2 5h20v14H2z M4 7v.5l8 5 8-5V7l-8 5z" fill-rule="evenodd"/></svg>info@frostvaleharborline.com</li>
      <li><svg viewBox="0 0 24 24"><path d="M12 2a10 10 0 1 0 0 20 10 10 0 0 0 0-20zm0 2c.9 0 2.2 2 2.7 5H9.3C9.8 6 11.1 4 12 4zM4.3 11h3a16 16 0 0 0 0 2h-3a8 8 0 0 1 0-2zm5 0h5.4a14 14 0 0 1 0 2H9.3a14 14 0 0 1 0-2zm7.4 0h3a8 8 0 0 1 0 2h-3a16 16 0 0 0 0-2zM9.3 15h5.4c-.5 3-1.8 5-2.7 5s-2.2-2-2.7-5z"/></svg>www.frostvaleharborline.com</li>
    </ul>
    <div class="brand">
      <span class="brand__dot"></span>
      <span class="brand__name">Frostvale Harborline LLC</span>
    </div>
  </section>
</main>
</body>
</html>
```